Broschüren-Design für Unternehmen, das die Begrünung von Bürogebäuden anbietet
Wir sind mit der Zusammenarbeit mit inkmolde äußerst zufrieden. Vielen Dank für das ganze Mitdenken und die wichtigen Rückfragen an uns (Format, Layout, Farben, Papierwahl)! :)
Zielgruppe
Unser Kerngeschäft besteht in der Begrünung von Bürogebäuden.
Das heißt, wir liefern und pflegen exotische und tropische immergrüne Planzen für zum Beispiel Eingangsbereiche, Atrien, sowie Einzel- und Großraumbüros.
Die Zielgruppe besteht fast ausschließlich aus gewerblichen Kunden.
Aufgabenstellung
Die Vorlage ist ein grober Entwurf und Vorschlag von uns. Es darf davon auch gerne abgewichen werden.
Die Broschüre soll uns als Unterstützung für Erstgespräche bei potentiellen Neukunden dienen und verbleibt beim Kunden. Sie soll unsere Firma, uns als Menschen und unsere Produkte und Dienstleistung kurz präsentieren und einen guten Eindruck hinterlassen.
Danach wünschen wir uns idealerweise eine Kontaktaufnahme durch den Kunden selbst.

```html
<!DOCTYPE html>
<html lang="de">
<head>
<meta charset="utf-8">
<title>Verdano Raumbegrünung – Broschüre</title>
<link href="https://fonts.googleapis.com/css2?family=Open+Sans:ital,wght@0,400;0,600;0,700;0,800;1,400;1,700;1,800&display=swap" rel="stylesheet">
<style>
:root{
  --bg:#e7e7e7;
  --paper:#f4f4f3;
  --white:#ffffff;
  --taupe:#d8d3cd;
  --green:#4f9e35;
  --ink:#2b2b2b;
  --muted:#555555;
  --red:#c8283c;
  --atrium:linear-gradient(165deg,#d9dee0 0%,#f3f3f1 22%,#b9c1c3 38%,#e6e6e3 50%,#8fae6c 64%,#4d7d34 74%,#c33a45 80%,#e9e9e6 86%,#5f8e3f 100%);
}
*{box-sizing:border-box;margin:0;padding:0}
html,body{width:1200px;height:3157px;overflow:hidden}
body{background:var(--bg);font-family:"Open Sans",Arial,sans-serif;color:var(--ink);position:relative}
.stage{position:absolute;left:0;width:1200px}
.stage--cover{top:120px}
.stage--inner{top:1260px}
.stage--outer{top:2300px}
.spread{display:flex;width:1120px;margin:0 auto;box-shadow:0 18px 40px rgba(0,0,0,.18)}
.panel{position:relative;width:280px;height:440px;overflow:hidden;background:var(--white)}
.photo{position:absolute}
.brand{display:flex;align-items:center;gap:6px;color:var(--green);font-weight:700;white-space:nowrap}
.brand__mark{flex:none;width:14px;height:14px;border:2px solid var(--green)}
.badge{position:absolute;border:2px solid var(--green);background:var(--white)}
.caption{position:absolute;background:rgba(255,255,255,.92);height:14px;padding:0 8px;font-size:7px;line-height:14px;color:var(--muted);white-space:nowrap}

/* cover */
.cover{width:520px;height:760px;margin:0 auto;background:var(--paper);position:relative;box-shadow:0 22px 50px rgba(0,0,0,.2)}
.cover .brand{position:absolute;right:36px;top:56px;font-size:30px;gap:12px}
.cover .brand__mark{width:32px;height:32px;border-width:3px}
.cover__intro{position:absolute;right:36px;left:70px;top:128px;font-size:12.5px;font-style:italic;font-weight:700;text-align:right;line-height:1.5}
.cover__photo{left:0;top:245px;width:520px;height:400px;background:var(--atrium)}
.cover .badge{left:36px;bottom:38px;width:130px;height:36px}

/* inner */
.quote{position:absolute;left:18px;right:14px;font-weight:800;font-style:italic;font-size:20px;line-height:1.2}
.block{position:absolute;left:16px;right:16px}
.block h3{font-size:13px;font-weight:800;font-style:italic;margin-bottom:6px;line-height:1.2}
.block p{font-size:9.5px;line-height:1.5;color:var(--muted)}
.note{position:absolute;left:16px;right:16px;background:var(--taupe);padding:10px 12px;font-size:9px;line-height:1.5;color:var(--ink)}
.band{position:absolute;left:0;right:0;background:var(--taupe)}
.leaf{position:absolute;right:12px;top:12px}

/* outer */
.team h2{font-size:15px;font-weight:800;position:absolute;left:16px;top:16px}
.team h2 small{font-size:7.5px;font-weight:600}
.team__row{position:absolute;left:14px;right:14px;top:46px;display:flex;justify-content:space-between}
.member{width:48px;text-align:center;font-size:7px;color:var(--muted);line-height:1.2}
.member .portrait{position:relative;width:46px;height:46px;background:linear-gradient(#c9ced3,#8d949b);margin:0 auto 4px}
.curious{position:absolute;left:0;right:0;top:128px;height:190px;background:var(--taupe);padding:16px}
.curious h3{font-size:16px;font-weight:800;line-height:1.15;margin-bottom:10px}
.curious p{font-size:9.5px;line-height:1.45;color:var(--ink);margin-bottom:6px}
.contact{position:absolute;left:16px;bottom:18px;font-size:8.5px;line-height:1.55;color:var(--muted)}
.contact .brand{font-size:14px;margin-bottom:8px}
.catalog h2{position:absolute;left:16px;top:16px;font-size:16px;font-weight:800}
.catalog h2 small{font-size:7.5px;font-weight:600}
.catalog__intro{position:absolute;left:16px;right:16px;top:44px;font-size:8.5px;line-height:1.5;color:var(--muted)}
.catalog__grid{position:absolute;left:14px;right:14px;top:100px;display:grid;grid-template-columns:1fr 1fr;gap:8px}
.item{background:var(--taupe);height:78px;display:flex;gap:6px;padding:5px}
.item .photo{position:relative;flex:none;width:42px;height:68px;background:linear-gradient(#f0f0ee 0%,#7fae55 12%,#3f6e2b 62%,var(--red) 64%,#a81f30 100%)}
.item b{display:block;font-size:8px;margin-bottom:3px}
.item span{font-size:7px;line-height:1.45;color:var(--muted)}
.catalog__foot{position:absolute;left:16px;right:16px;bottom:16px;font-size:8px;line-height:1.4;color:var(--muted)}
.catalog__foot .brand{font-size:12px;margin-bottom:5px}
.mini{background:var(--paper)}
.mini .brand{position:absolute;right:16px;top:24px;font-size:14px}
.mini__intro{position:absolute;left:18px;right:16px;top:52px;font-size:7.5px;font-style:italic;font-weight:700;text-align:right;line-height:1.5}
.mini .photo{left:0;top:118px;width:280px;height:230px;background:var(--atrium)}
.mini .badge{left:16px;bottom:28px;width:70px;height:20px}
</style>
</head>
<body>

<section class="stage stage--cover">
  <article class="cover">
    <div class="brand"><span class="brand__mark"></span>Verdano Raumbegrünung</div>
    <p class="cover__intro">Wir sind Verdano Raumbegrünung, das Familienunternehmen in der Raumbegrünung und Hydrokultur. In unserer tagtäglichen Arbeit liefern und pflegen wir Pflanzen in Büros, Versicherungen, Banken, Ärztezentren, Schulen, Schwimmbädern und Behörden.</p>
    <div class="photo cover__photo" role="img" aria-label="Foto: helles Atrium mit großen Grünpflanzen in roten Gefäßen"></div>
    <div class="badge" role="img" aria-label="Zertifikatssiegel"></div>
  </article>
</section>

<section class="stage stage--inner">
  <div class="spread">
    <div class="panel">
      <div class="photo" style="inset:0;background:linear-gradient(172deg,#9aa0a0 0%,#d8cf8a 14%,#7fae4e 30%,#3f7a2f 48%,#5a8e3c 60%,#7a5a3d 78%,#4b4b4b 100%)" role="img" aria-label="Foto: Baum im Innenhof eines Bürogebäudes"></div>
      <span class="caption" style="left:60px;bottom:56px">Innenhof, Bürogebäude</span>
    </div>
    <div class="panel">
      <div class="photo" style="left:0;top:0;width:280px;height:120px;background:linear-gradient(160deg,#c7d0d2 0%,#e5e8e8 30%,#7a9a66 58%,#3f7030 72%,var(--red) 86%,#9e1f2c 100%)" role="img" aria-label="Foto: Pflanzen in roten Gefäßen im Foyer"></div>
      <p class="quote" style="top:138px">„Wir kümmern uns mit unserem Team gerne um Ihre bestehenden Pflanzen.“</p>
      <div class="photo" style="left:0;top:280px;width:280px;height:160px;background:linear-gradient(150deg,#eeeeec 0%,#c9d2c3 25%,#6a9a4a 55%,#3a6a2a 80%,#2d4f22 100%)" role="img" aria-label="Foto: Pflanzgefäß mit Blattpflanzen"></div>
      <span class="caption" style="left:18px;bottom:16px">Empfangsbereich</span>
    </div>
    <div class="panel">
      <div class="block" style="top:16px">
        <h3>Pflege &amp; Wartung<br>Bestandspflanzen</h3>
        <p>Wir kümmern uns regelmäßig um Ihre vorhandenen Pflanzen: Wir gießen, düngen, schneiden und reinigen sie fachgerecht. So bleiben Ihre Räume das ganze Jahr über grün und gepflegt.</p>
      </div>
      <div class="note" style="top:118px">Kranke oder schwache Pflanzen tauschen wir schnell gegen gesunde aus – ganz ohne Aufwand für Sie.</div>
      <div class="photo" style="left:0;top:180px;width:280px;height:110px;background:linear-gradient(180deg,#eef0ef 0%,#d9dedb 25%,#8fae7a 50%,#4f7a3c 72%,#c8283c 86%,#dcdcdc 100%)" role="img" aria-label="Foto: große Palme in hellem Empfangsbereich"></div>
      <div class="block" style="top:304px">
        <h3>Neubegrünung &amp; Lieferung</h3>
        <p>Wir planen mit Ihnen die passende Begrünung für Ihre Räume und liefern alle Pflanzen samt Gefäßen direkt zu Ihnen. Auf Wunsch übernehmen wir auch die Aufstellung und die erste Pflege vor Ort.</p>
      </div>
    </div>
    <div class="panel">
      <div class="band" style="top:0;height:104px"></div>
      <div class="block" style="top:16px;right:56px">
        <h3>Platz für weiteren Text</h3>
        <p>Platz für weiteren Text – Platz für weiteren Text – Platz für weiteren Text – Platz für weiteren Text – Platz für weiteren Text.</p>
      </div>
      <svg class="leaf" width="40" height="28" viewBox="0 0 40 28" aria-hidden="true"><path d="M2 26 C6 6 24 2 38 2 C36 16 24 26 2 26 Z M2 26 L30 8" fill="none" stroke="#fff" stroke-width="1.5"/></svg>
      <div class="photo" style="left:0;top:104px;width:280px;height:336px;background:linear-gradient(170deg,#3a3328 0%,#8a7a52 20%,#6d7a2e 38%,#8c9a3a 50%,#4a4a30 66%,#2e2c26 82%,#1f1e1b 100%)" role="img" aria-label="Foto: begrünte Wand in einer Kantine"></div>
      <span class="caption" style="right:16px;bottom:16px">Mooswand, Kantine</span>
    </div>
  </div>
</section>

<section class="stage stage--outer">
  <div class="spread">
    <div class="panel team">
      <h2>Unser Team <small>(oder eine andere Headline)</small></h2>
      <div class="team__row">
        <div class="member"><div class="portrait" role="img" aria-label="Porträtfoto Teammitglied"></div>Paul Brandt</div>
        <div class="member"><div class="portrait" role="img" aria-label="Porträtfoto Teammitglied"></div>Anna Kessler</div>
        <div class="member"><div class="portrait" role="img" aria-label="Porträtfoto Teammitglied"></div>Tim Ulmer</div>
        <div class="member"><div class="portrait" role="img" aria-label="Porträtfoto Teammitglied"></div>Jan Nowak</div>
        <div class="member"><div class="portrait" role="img" aria-label="Porträtfoto Teammitglied"></div>Lea Seidel</div>
      </div>
      <div class="curious">
        <h3>Sie sind<br>neugierig geworden?</h3>
        <p>Nehmen Sie Kontakt mit uns auf! Wir beraten Sie gerne persönlich vor Ort.</p>
        <p>Wir erstellen Ihnen ein unverbindliches Angebot für Ihre Räume.</p>
        <p>Gerne liefern wir Ihnen auch eine Probepflanze für einige Wochen.</p>
      </div>
      <div class="contact">
        <div class="brand"><span class="brand__mark"></span>Verdano Raumbegrünung</div>
        Verdano Raumbegrünung GmbH &amp; Co. KG<br>Gartenweg 12 · 31234 Musterstadt<br>Tel. 0511 123 456<br>info@verdano-raum.de · verdano-raum.de
      </div>
    </div>
    <div class="panel">
      <div class="photo" style="inset:0;background:linear-gradient(160deg,#2f5a24 0%,#5f9a3e 22%,#2d4f22 42%,#6aa447 58%,#3a6a2a 74%,#a8263a 88%,#5a1a22 100%)" role="img" aria-label="Foto: dichte Pflanzenwand mit roten Anthurien"></div>
      <span class="caption" style="right:16px;bottom:24px">Pflanzenwand</span>
    </div>
    <div class="panel catalog">
      <h2>Katalog <small>(Auszug)</small></h2>
      <p class="catalog__intro">Eine Auswahl unserer beliebtesten Pflanzen für Büro und Empfang. Alle Pflanzen erhalten Sie in Hydrokultur mit passendem Gefäß – in vielen Farben und Größen.</p>
      <div class="catalog__grid">
        <div class="item"><div class="photo" role="img" aria-label="Foto: Topfpflanze"></div><div><b>Pflanzenname</b><span>Höhe ca. 120 cm<br>Pflege: leicht<br>Gefäß rot</span></div></div>
        <div class="item"><div class="photo" role="img" aria-label="Foto: Topfpflanze"></div><div><b>Pflanzenname</b><span>Höhe ca. 90 cm<br>Pflege: leicht<br>Gefäß rot</span></div></div>
        <div class="item"><div class="photo" role="img" aria-label="Foto: Topfpflanze"></div><div><b>Pflanzenname</b><span>Höhe ca. 150 cm<br>Pflege: mittel<br>Gefäß rot</span></div></div>
        <div class="item"><div class="photo" role="img" aria-label="Foto: Topfpflanze"></div><div><b>Pflanzenname</b><span>Höhe ca. 100 cm<br>Pflege: leicht<br>Gefäß rot</span></div></div>
        <div class="item"><div class="photo" role="img" aria-label="Foto: Topfpflanze"></div><div><b>Pflanzenname</b><span>Höhe ca. 80 cm<br>Pflege: leicht<br>Gefäß rot</span></div></div>
        <div class="item"><div class="photo" role="img" aria-label="Foto: Topfpflanze"></div><div><b>Pflanzenname</b><span>Höhe ca. 130 cm<br>Pflege: mittel<br>Gefäß rot</span></div></div>
      </div>
      <div class="catalog__foot">
        <div class="brand"><span class="brand__mark"></span>Verdano Raumbegrünung</div>
        Weitere Pflanzen finden Sie in unserem Gesamtkatalog.
      </div>
    </div>
    <div class="panel mini">
      <div class="brand"><span class="brand__mark"></span>Verdano Raumbegrünung</div>
      <p class="mini__intro">Wir sind Verdano Raumbegrünung, das Familienunternehmen in der Raumbegrünung und Hydrokultur. In unserer tagtäglichen Arbeit liefern und pflegen wir Pflanzen in Büros, Versicherungen, Banken, Schulen und Behörden.</p>
      <div class="photo" role="img" aria-label="Foto: helles Atrium mit Grünpflanzen in roten Gefäßen"></div>
      <div class="badge" role="img" aria-label="Zertifikatssiegel"></div>
    </div>
  </div>
</section>

</body>
</html>
```